Indy Film Production Company/Studio

We need a business card designed from an existing logo. We are a digital studio/production company that caters to creating genre entertainment, like Action, Horror, and martial arts. The card along with the logo will be used to Brand the company from letter heads to banners. The design will also be used for postcards and Brochures. It should be professional and masculine.
Updates

Thank you to all the designers who have participated. I'm narrowing down who it will be. Thank you again.

Target Market(s)

Investors, Networks, Producers, and actors

Industry/Entity Type

Film Production

Contact Information for Business Card

Teodoro Valbuena
Producer/Writer/Director
www.kestrelpicturehouse.example

Requirements
Must have
• Website address, Facebook icon and Twitter icon possibly in the back of the card.
Nice to have
• Logline of Company: Follow The Action.

```html
<!DOCTYPE html>
<html lang="en">
<head>
<meta charset="utf-8">
<title>Kestrel Picture House – Business Card</title>
<link rel="stylesheet" href="https://fonts.googleapis.com/css2?family=Fira+Sans:wght@400;700&display=swap">
<style>
  :root {
    --backdrop: #d8d4cf;
    --card: #f1f0ee;
    --brand-red: #d21f28;
    --band-red-light: #e3262e;
    --band-red-dark: #a80e17;
    --stripe-dark: #1c1c1e;
    --ink-light: #f3e6e6;
    --ink-muted: #e9b9bb;
  }
  * { margin: 0; padding: 0; box-sizing: border-box; }
  html, body {
    width: 1200px; height: 969px; overflow: hidden;
    background: var(--backdrop);
    font-family: "Fira Sans", Arial, sans-serif;
  }
  .card {
    position: absolute; left: 100px; top: 200px;
    width: 1000px; height: 568px;
    background: var(--card);
    box-shadow: 0 10px 30px rgba(0,0,0,.18);
    overflow: hidden;
  }
  .card-band { position: absolute; inset: 0; }
  .brand-name {
    position: absolute; left: 48px; top: 62px;
    color: var(--brand-red);
    font-weight: 700; font-size: 70px; line-height: 1.02;
    text-transform: uppercase; letter-spacing: 1px;
  }
  .person { position: absolute; left: 48px; top: 440px; }
  .person-name {
    color: var(--ink-light); font-size: 31px; font-weight: 400;
    text-transform: uppercase; letter-spacing: 1.5px;
  }
  .person-title {
    margin-top: 8px;
    color: var(--ink-muted); font-size: 22px;
    text-transform: uppercase; letter-spacing: 1px;
  }
  .contact {
    position: absolute; right: 40px; top: 360px;
    display: flex; flex-direction: column; align-items: flex-end; gap: 11px;
    color: var(--ink-light); font-size: 22px;
  }
  .social { display: flex; gap: 6px; margin-bottom: 6px; }
  .social-square { width: 32px; height: 32px; background: var(--ink-light); opacity: .85; }
  .contact-line { display: flex; align-items: center; gap: 14px; }
  .contact-icon { width: 24px; height: 24px; flex: none; }
</style>
</head>
<body>
  <div class="card">
    <svg class="card-band" viewBox="0 0 1000 568" aria-hidden="true">
      <defs>
        <linearGradient id="bandFill" x1="0" y1="0" x2="1" y2="1">
          <stop offset="0" stop-color="var(--band-red-light)"/>
          <stop offset="1" stop-color="var(--band-red-dark)"/>
        </linearGradient>
      </defs>
      <path d="M0,340 L626,340 L609,362 L0,362 Z" fill="var(--stripe-dark)"/>
      <path d="M0,368 L604,368 L648,311 L1000,311 L1000,568 L0,568 Z" fill="url(#bandFill)"/>
    </svg>

    <div class="brand-name">Kestrel<br>Picture House</div>

    <div class="person">
      <div class="person-name">Teodoro Valbuena</div>
      <div class="person-title">Producer/Writer/Director</div>
    </div>

    <div class="contact">
      <div class="social">
        <div class="social-square"></div>
        <div class="social-square"></div>
      </div>
      <div class="contact-line">
        <span>555 0142 3387</span>
        <svg class="contact-icon" viewBox="0 0 24 24" aria-hidden="true">
          <path d="M6 3 L9.5 3 L11 8 L8.5 9.8 C9.6 12.3 11.7 14.4 14.2 15.5 L16 13 L21 14.5 L21 18 C21 19.7 19.7 21 18 21 C10 21 3 14 3 6 C3 4.3 4.3 3 6 3 Z" fill="var(--ink-light)"/>
        </svg>
      </div>
      <div class="contact-line">
        <span>teodoro@kestrelpicturehouse.example</span>
        <svg class="contact-icon" viewBox="0 0 24 24" aria-hidden="true">
          <rect x="2" y="5" width="20" height="14" fill="var(--ink-light)"/>
          <path d="M2 5 L12 13 L22 5" fill="none" stroke="var(--band-red-dark)" stroke-width="1.6"/>
        </svg>
      </div>
      <div class="contact-line">
        <span>www.kestrelpicturehouse.example</span>
        <svg class="contact-icon" viewBox="0 0 24 24" aria-hidden="true">
          <circle cx="12" cy="12" r="10" fill="var(--ink-light)"/>
          <ellipse cx="12" cy="12" rx="4" ry="10" fill="none" stroke="var(--band-red-dark)" stroke-width="1.4"/>
          <path d="M2 12 H22" stroke="var(--band-red-dark)" stroke-width="1.4"/>
        </svg>
      </div>
    </div>
  </div>
</body>
</html>
```